Business card design Needed for new logo / Construction business, home extensions and new builds

We need a business card design using our new logo files which i will attach to this project :)

We are a small construction business specialising in home extensions, new builds and property development. We are very ambitious and would appreciate professional and elegant designs for our new business card.

Very serious about using the services on MakerQuarry and recently acquired our new logo from here :)

Please get involved, i will feedback when i can as i am very busy but can respond daily, thanks

Target Market(s)

People that want to build onto their houses, new building developments or adding too their existing property

Industry/Entity Type

Construction

Contact Information for Business Card

Renwick Tolliver Construction, Lionel Ashby (Managing Director), Tel 07822254961, email - info@renwick-tolliver, www.renwick-tolliver.co.uk

Colors

Designer to choose colors to be used in the design.

Requirements
Must have
• I like a deep grey on the back please. A lot of you have provided black from and back, try mixing things up a little. The black looks cool 😎 Thanks

```html
<!DOCTYPE html>
<html lang="en">
<head>
<meta charset="utf-8">
<title>Renwick Tolliver Construction – Business Card</title>
<link href="https://fonts.googleapis.com/css2?family=Open+Sans:wght@400;600;700&display=swap" rel="stylesheet">
<style>
  :root {
    --backdrop: #2a2a2d;
    --card-black: #1c1c1f;
    --gold-light: #f3d27a;
    --gold: #d9a53a;
    --gold-deep: #a8761c;
    --silver-light: #f2f2f2;
    --silver: #b9bcc0;
    --white: #ffffff;
    --back-grey: #8f9398;
    --back-grey-light: #b4b8bc;
    --back-grey-deep: #73777c;
  }
  * { box-sizing: border-box; margin: 0; padding: 0; }
  html, body {
    width: 1200px; height: 780px; overflow: hidden;
    background: var(--backdrop);
    font-family: "Open Sans", Arial, sans-serif;
  }
  .canvas {
    position: relative; width: 1200px; height: 780px;
    display: flex; align-items: center; justify-content: center; gap: 50px;
  }
  .card {
    position: relative; width: 540px; height: 309px;
    border-radius: 4px; overflow: hidden;
    box-shadow: 0 14px 30px rgba(0,0,0,.45);
  }

  /* Front */
  .card-front { background: var(--card-black); color: var(--white); }
  .brand {
    position: absolute; top: 46px; right: 44px; width: 250px;
    text-align: center;
  }
  .brand-name {
    font-size: 19px; font-weight: 600; letter-spacing: 1.5px;
    color: var(--gold); text-transform: uppercase; line-height: 1.35;
  }
  .person { position: absolute; left: 40px; top: 60px; }
  .person-name { font-size: 30px; font-weight: 700; line-height: 1.1; }
  .person-name .first { color: var(--silver); }
  .person-name .last { color: var(--gold); }
  .person-role { font-size: 14px; margin-top: 6px; color: var(--silver-light); }
  .divider {
    position: absolute; left: 262px; top: 150px; width: 1px; height: 92px;
    background: linear-gradient(var(--silver-light), rgba(255,255,255,0.15));
  }
  .contacts { position: absolute; left: 286px; top: 152px; list-style: none; }
  .contacts li {
    display: flex; align-items: center; gap: 10px;
    font-size: 15px; line-height: 30px; color: var(--white);
  }
  .contacts svg { width: 15px; height: 15px; fill: var(--gold); flex: none; }
  .address-band {
    position: absolute; left: 0; right: 0; bottom: 22px; height: 30px;
    background: linear-gradient(180deg, var(--gold-light), var(--gold) 55%, var(--gold-deep));
    display: flex; align-items: center; padding-left: 40px;
    font-size: 14px; font-weight: 600; color: var(--white);
    text-shadow: 0 1px 1px rgba(0,0,0,.25);
  }

  /* Back */
  .card-back {
    background: linear-gradient(120deg, var(--back-grey-deep), var(--back-grey) 45%, var(--back-grey-light));
  }
  .back-pattern { position: absolute; inset: 0; }
  .back-brand {
    position: absolute; right: 26px; bottom: 22px;
    display: flex; align-items: center; gap: 6px;
    font-size: 9px; font-weight: 600; letter-spacing: .6px;
    text-transform: uppercase; color: var(--white);
  }
  .back-brand .mark { width: 10px; height: 10px; background: var(--white); }
</style>
</head>
<body>
<main class="canvas">
  <section class="card card-front" aria-label="Business card front">
    <div class="person">
      <h1 class="person-name"><span class="first">Lionel</span> <span class="last">Ashby</span></h1>
      <p class="person-role">Managing Director</p>
    </div>

    <div class="brand">
      <p class="brand-name">Renwick Tolliver<br>Construction</p>
    </div>

    <div class="divider"></div>

    <ul class="contacts">
      <li>
        <svg viewBox="0 0 24 24" aria-hidden="true"><path d="M6.6 10.8a15.1 15.1 0 0 0 6.6 6.6l2.2-2.2a1 1 0 0 1 1-.25 11.4 11.4 0 0 0 3.6.57 1 1 0 0 1 1 1V20a1 1 0 0 1-1 1A17 17 0 0 1 3 4a1 1 0 0 1 1-1h3.5a1 1 0 0 1 1 1c0 1.25.2 2.45.57 3.57a1 1 0 0 1-.25 1z"/></svg>
        0782 225 4961
      </li>
      <li>
        <svg viewBox="0 0 24 24" aria-hidden="true"><path d="M12 2a10 10 0 1 0 0 20 10 10 0 0 0 0-20zm6.9 6h-2.9a15.6 15.6 0 0 0-1.4-3.6A8 8 0 0 1 18.9 8zM12 4c.8 1.2 1.5 2.5 1.9 4h-3.8c.4-1.5 1.1-2.8 1.9-4zM4.3 14a8 8 0 0 1 0-4h3.4a16 16 0 0 0 0 4zm.8 2h2.9c.3 1.3.8 2.5 1.4 3.6A8 8 0 0 1 5.1 16zM8 8H5.1a8 8 0 0 1 4.3-3.6C8.8 5.5 8.3 6.7 8 8zm4 12c-.8-1.2-1.5-2.5-1.9-4h3.8c-.4 1.5-1.1 2.8-1.9 4zm2.3-6H9.7a14.7 14.7 0 0 1 0-4h4.6a14.7 14.7 0 0 1 0 4zm.3 5.6c.6-1.1 1.1-2.3 1.4-3.6h2.9a8 8 0 0 1-4.3 3.6zm1.7-5.6a16 16 0 0 0 0-4h3.4a8 8 0 0 1 0 4z"/></svg>
        info@renwick-tolliver.co.uk
      </li>
      <li>
        <svg viewBox="0 0 24 24" aria-hidden="true"><path d="M20 4H4a2 2 0 0 0-2 2v12a2 2 0 0 0 2 2h16a2 2 0 0 0 2-2V6a2 2 0 0 0-2-2zm0 4-8 5-8-5V6l8 5 8-5z"/></svg>
        www.renwick-tolliver.co.uk
      </li>
    </ul>

    <div class="address-band">Halden Road, Westbury Poole, BH14 6QR</div>
  </section>

  <section class="card card-back" aria-label="Business card back">
    <div class="back-pattern" role="img" aria-label="Repeating brand-mark pattern in soft silver tones across the deep grey back"></div>
    <div class="back-brand"><span class="mark"></span>Renwick Tolliver Construction</div>
  </section>
</main>
</body>
</html>
```